Business Card Design

Online clothing womens clothing store, I sell my clothing online and at the markets.

i would like the attached picture on the front of the card and the contact information on the back.

Industry/Entity Type

Business

Contact Information for Business Card

Marlow Thread
Karen Whitfield
(Instagram symbol) _marlow_thread_
(Facebook symbol) www.fakebookexample.com/marlowthreadau/

W : www.marlowthread.example.au
E : info@marlowthread.example.au
P : 0498716204

```html
<!DOCTYPE html>
<html lang="en">
<head>
<meta charset="utf-8">
<title>Marlow Thread — Business Card</title>
<link rel="stylesheet" href="https://fonts.googleapis.com/css2?family=Questrial&family=Marcellus+SC&family=Arimo&display=swap">
<style>
  :root {
    --page-bg: #d9d8d6;
    --card-black: #050505;
    --ink-white: #ffffff;
    --rule: #e6e6e6;
    --photo-light: #d4d4d4;
    --photo-mid: #9a9a9a;
    --photo-dark: #3a3a3a;
  }
  * { box-sizing: border-box; margin: 0; padding: 0; }
  html, body {
    width: 1200px; height: 864px; overflow: hidden;
    background: var(--page-bg);
  }
  .sheet {
    width: 1200px; height: 864px;
    display: flex; align-items: center; justify-content: center; gap: 40px;
  }
  .card {
    width: 540px; height: 309px;
    position: relative; overflow: hidden;
    box-shadow: 0 6px 18px rgba(0,0,0,0.25);
  }
  /* Contact side */
  .card--contact {
    background: var(--card-black);
    color: var(--ink-white);
    text-align: center;
  }
  .brand-name {
    position: absolute; top: 34px; left: 0; right: 0;
    font-family: "Questrial", sans-serif;
    font-size: 30px; letter-spacing: 9px;
    text-transform: uppercase;
  }
  .brand-rule {
    position: absolute; top: 86px; left: 46px; right: 46px;
    height: 1px; background: var(--rule);
  }
  .person-name {
    position: absolute; top: 102px; left: 0; right: 0;
    font-family: "Marcellus SC", serif;
    font-size: 23px; letter-spacing: 4px;
  }
  .contact-list {
    position: absolute; top: 150px; left: 0; right: 0;
    list-style: none;
    font-family: "Arimo", sans-serif;
    font-size: 16px; line-height: 22px;
  }
  /* Image side */
  .card--image { background: var(--photo-light); }
  .card--image svg { position: absolute; inset: 0; }
  .image-wordmark {
    position: absolute; left: 40px; bottom: 40px;
    font-family: "Questrial", sans-serif;
    font-size: 44px; letter-spacing: 3px;
    text-transform: uppercase;
    color: var(--ink-white);
  }
</style>
</head>
<body>
<main class="sheet">
  <section class="card card--contact" aria-label="Business card, contact side">
    <div class="brand-name">Marlow Thread</div>
    <div class="brand-rule"></div>
    <div class="person-name">Karen Whitfield</div>
    <ul class="contact-list">
      <li>0498716204</li>
      <li>marlowthreadau</li>
      <li>marlow_thread</li>
      <li>www.marlowthread.example.au</li>
      <li>info@marlowthread.example.au</li>
    </ul>
  </section>

  <section class="card card--image" aria-label="Business card, image side">
    <svg width="540" height="309" viewBox="0 0 540 309" role="img" aria-label="Black and white smoky fashion photograph of a woman">
      <defs>
        <radialGradient id="smoke" cx="0.72" cy="0.55" r="0.6">
          <stop offset="0" stop-color="var(--photo-dark)"/>
          <stop offset="0.55" stop-color="var(--photo-mid)"/>
          <stop offset="1" stop-color="var(--photo-light)"/>
        </radialGradient>
      </defs>
      <rect width="540" height="309" fill="url(#smoke)"/>
    </svg>
    <div class="image-wordmark">Marlow Thread</div>
  </section>
</main>
</body>
</html>
```